Veltrane Group Business Card Design

The CEO is looking for a new trendy look for his business card.
You can stay with current branding or come up with something new/creative. It can be 3D, including Medical Office buildings. You can use our logo in a variety of colors. Please include name, title, company name, company website, email address, cell number

Target Market(s)

Real Estate Development and Construction

Industry/Entity Type

Health care real estate

Contact Information for Business Card

Rohesh Kamdar, CEO M-604.781.2249 E-roheshkamdar@veltrane.com Address:4180 Lindqvist Ave, Tampa, FL 33482 www.veltrane.com

Font styles to use
Other font styles liked:
• Be creative

Requirements
Must have
• Creative, trendy look
Nice to have
• Please go to our website to get a feel- www. veltrane.com
Should not have
• small fonts

```html
<!DOCTYPE html>
<html lang="en">
<head>
<meta charset="UTF-8">
<title>Veltrane Group – Business Card</title>
<link href="https://fonts.googleapis.com/css2?family=Montserrat:wght@400;700;800&display=swap" rel="stylesheet">
<style>
  :root {
    --bg: #1b1b1d;
    --card-white: #ffffff;
    --card-white-end: #eff1f6;
    --card-black: #1a1a1c;
    --card-black-end: #0c0c0d;
    --brand-red: #b3212f;
    --brand-navy: #1c2d52;
    --text-grey: #4a4a4f;
    --edge-red: #7a1820;
  }
  * { margin: 0; padding: 0; box-sizing: border-box; }
  html, body { width: 1200px; height: 800px; overflow: hidden; }
  body {
    background: var(--bg);
    font-family: "Montserrat", Arial, sans-serif;
    display: flex;
    align-items: center;
    justify-content: center;
    gap: 60px;
  }
  .card {
    width: 340px;
    height: 580px;
    border-radius: 36px;
    position: relative;
    box-shadow: 0 0 0 1.5px var(--edge-red), 0 18px 40px rgba(0,0,0,.55);
  }
  .card--front {
    background: linear-gradient(160deg, var(--card-white) 40%, var(--card-white-end));
    padding: 64px 36px 48px;
  }
  .card--back {
    background: linear-gradient(160deg, var(--card-black), var(--card-black-end));
    display: flex;
    align-items: center;
    justify-content: center;
  }
  .holder-name {
    color: var(--brand-red);
    font-weight: 800;
    font-size: 25px;
    letter-spacing: 1px;
    text-transform: uppercase;
    line-height: 1.1;
  }
  .holder-title {
    color: var(--brand-navy);
    font-weight: 700;
    font-size: 16px;
    letter-spacing: 1px;
    margin-top: 2px;
    padding-left: 14px;
  }
  .address {
    color: var(--text-grey);
    font-size: 15px;
    line-height: 1.35;
    margin-top: 26px;
    padding-left: 32px;
  }
  .contact-list {
    list-style: none;
    margin-top: 22px;
    padding-left: 32px;
  }
  .contact-list li {
    display: flex;
    align-items: center;
    gap: 10px;
    color: var(--text-grey);
    font-size: 14px;
    line-height: 1.75;
    white-space: nowrap;
  }
  .contact-list svg { width: 15px; height: 15px; flex: none; fill: var(--brand-red); }
  .wordmark {
    position: absolute;
    right: 36px;
    bottom: 56px;
    color: var(--brand-red);
    font-weight: 800;
    font-size: 38px;
    letter-spacing: -0.5px;
    line-height: 1;
    text-align: right;
  }
  .wordmark--back { position: static; font-size: 40px; text-align: center; }
</style>
</head>
<body>
  <section class="card card--front" aria-label="Business card front">
    <h1 class="holder-name">Rohesh Kamdar</h1>
    <p class="holder-title">CEO</p>
    <p class="address">4180 Lindqvist Ave,<br>Tampa, FL 33482</p>
    <ul class="contact-list">
      <li>
        <svg viewBox="0 0 16 16" aria-hidden="true"><path d="M4 1h8a1 1 0 0 1 1 1v12a1 1 0 0 1-1 1H4a1 1 0 0 1-1-1V2a1 1 0 0 1 1-1zm1 2v9h6V3zm3 10a.8.8 0 1 0 0 .01z"/></svg>
        604.781.2249
      </li>
      <li>
        <svg viewBox="0 0 16 16" aria-hidden="true"><path d="M1 4h14v9H1zm1.5 1 5.5 4 5.5-4z"/></svg>
        roheshkamdar@veltrane.com
      </li>
      <li>
        <svg viewBox="0 0 16 16" aria-hidden="true"><circle cx="8" cy="8" r="7"/></svg>
        www.veltrane.com
      </li>
    </ul>
    <p class="wordmark">Veltrane Group</p>
  </section>

  <section class="card card--back" aria-label="Business card back">
    <p class="wordmark wordmark--back">Veltrane<br>Group</p>
  </section>
</body>
</html>
```